Business Card Design - Amberfield Court

We are looking at a new design for our business cards that has a modern and professional look. We run a residential aged care facility focussing on the care of residents. The cards will be used for potential clients, consultants and business opportunities in this sector. Blue and white is our main colours and would to see these colours incorporated in the design.
Industry/Entity Type
Business
Contact Information for Business Card
Amberfield Court, Darren Walsh, dwalsh@amberfieldcourt.com.au, Finance Manager, 0472 639 208, BCom, 37 Marrabel Crescent, Brindle Vale, Qld 4093.
Look and feel
Each slider illustrates characteristics of the customer's brand and the style your logo design should communicate.

```html
<!DOCTYPE html>
<html lang="en">
<head>
<meta charset="utf-8">
<title>Amberfield Court – Business Card</title>
<link rel="stylesheet" href="https://fonts.googleapis.com/css2?family=Open+Sans:ital,wght@0,300;0,400;0,600;1,400&display=swap">
<style>
  :root {
    --backdrop: #ece9e4;
    --blue-light: #7fb6c9;
    --blue-mid: #5a98ae;
    --blue-deep: #3b7690;
    --slate: #2f5666;
    --white: #ffffff;
    --paper: #f6f6f5;
    --taupe: #c9c0b8;
    --text-light: #eaf4f7;
  }
  * { margin: 0; padding: 0; box-sizing: border-box; }
  html, body { width: 1200px; height: 1023px; overflow: hidden; }
  body {
    background: var(--backdrop);
    font-family: "Open Sans", Arial, sans-serif;
    position: relative;
  }
  .card {
    position: absolute;
    left: 250px;
    width: 700px;
    height: 400px;
    overflow: hidden;
    box-shadow: 0 6px 18px rgba(0,0,0,0.18);
  }
  .card--front { top: 70px; }
  .card--back  { top: 550px; background: linear-gradient(135deg, var(--blue-light), var(--blue-mid) 50%, var(--blue-deep)); }
  .card-art { position: absolute; inset: 0; }

  .contact { position: absolute; left: 48px; top: 58px; color: var(--text-light); }
  .contact__name { font-weight: 600; font-size: 27px; letter-spacing: 1px; color: var(--slate); text-transform: uppercase; }
  .contact__role { font-size: 14px; letter-spacing: 0.5px; text-transform: uppercase; margin-top: 10px; }
  .contact__lines { list-style: none; margin-top: 12px; font-size: 14px; line-height: 25px; }
  .contact__lines li { display: flex; align-items: center; gap: 8px; }
  .contact__lines .upper { text-transform: uppercase; }
  .contact__icon { width: 13px; height: 13px; flex: none; }

  .brand { position: absolute; right: 36px; top: 80px; display: flex; align-items: center; gap: 16px; }
  .brand__dot { width: 70px; height: 70px; border-radius: 50%; background: var(--blue-mid); flex: none; }
  .brand__name { font-weight: 300; font-size: 27px; letter-spacing: 3px; color: var(--slate); text-transform: uppercase; line-height: 1.15; }

  .back-brand { position: absolute; left: 52px; top: 56px; }
  .back-brand__name { font-weight: 300; font-size: 36px; letter-spacing: 5px; color: var(--slate); text-transform: uppercase; }
  .back-brand__tagline { font-style: italic; font-size: 19px; color: var(--text-light); margin-top: 6px; letter-spacing: 0.5px; }
  .back-decor {
    position: absolute; right: 40px; bottom: 0; width: 330px; height: 210px;
    border-radius: 165px 165px 0 0;
    background: radial-gradient(ellipse at 50% 60%, rgba(47,86,102,0.35), rgba(47,86,102,0.08) 70%, rgba(47,86,102,0));
  }
</style>
</head>
<body>
  <section class="card card--front" aria-label="Business card front">
    <svg class="card-art" viewBox="0 0 700 400" width="700" height="400" aria-hidden="true">
      <defs>
        <linearGradient id="front-blue" x1="0" y1="0" x2="1" y2="1">
          <stop offset="0" stop-color="#7fb6c9"/>
          <stop offset="0.5" stop-color="#5a98ae"/>
          <stop offset="1" stop-color="#3b7690"/>
        </linearGradient>
      </defs>
      <rect width="700" height="400" fill="url(#front-blue)"/>
      <path d="M372 0 C330 120 520 250 452 400 L700 400 L700 0 Z" fill="#c9c0b8"/>
      <path d="M388 0 C348 120 538 250 470 400 L700 400 L700 0 Z" fill="#f6f6f5"/>
    </svg>

    <div class="contact">
      <p class="contact__name">Darren Walsh</p>
      <p class="contact__role">Finance Manager</p>
      <ul class="contact__lines">
        <li>
          <svg class="contact__icon" viewBox="0 0 13 13"><rect x="3" y="0.5" width="7" height="12" rx="1.5" fill="none" stroke="#eaf4f7" stroke-width="1.3"/><circle cx="6.5" cy="10.3" r="0.9" fill="#eaf4f7"/></svg>
          0472 639 208
        </li>
        <li>
          <svg class="contact__icon" viewBox="0 0 13 13"><rect x="0.7" y="2.5" width="11.6" height="8" fill="none" stroke="#eaf4f7" stroke-width="1.2"/><path d="M0.7 2.5 L6.5 7 L12.3 2.5" fill="none" stroke="#eaf4f7" stroke-width="1.2"/></svg>
          dwalsh@amberfieldcourt.com.au
        </li>
        <li class="upper">BCom, 37 Marrabel Crescent</li>
        <li class="upper">Brindle Vale, Qld 4093.</li>
      </ul>
    </div>

    <div class="brand">
      <span class="brand__dot" aria-hidden="true"></span>
      <p class="brand__name">Amberfield<br>Court</p>
    </div>
  </section>

  <section class="card card--back" aria-label="Business card back">
    <div class="back-brand">
      <p class="back-brand__name">Amberfield Court</p>
      <p class="back-brand__tagline">Care, Comfort, Community</p>
    </div>
    <div class="back-decor" role="img" aria-label="Faint large brand emblem area"></div>
  </section>
</body>
</html>
```